Business Card Design Project

We have recently completed CraftHive projects for a new logo and wesbite.
We now require new business cards.
We hand out very little printed material to clients as all information is online. When we do hand out something, like a business card, we want it to have real impact and make a statement about the quality and professionalism of our company.
We have an idea of what we want our card to look like but we want a designer to make sure they have impact and look great.
Our requirements are…
Size: 85mm X 55mm - Landscape
Front of card: Logo plus the following contact information.
Dennis Marlow
Operations Manager
Phone +44(0) 1632 xxx xxx
Mobile +44(0) 7700 xxx xxx
Email denmo@korvantix.example
Address 17 Pellick Row, Aberdeen AB12 9QZ
Website www.korvantix.example
How you layout the front of the card is up to you, we would like to see some different ideas. Attached are two versions of our logo that may be used.
Back of card: We would like this to be simple but again have impact. Our current thought is to have the logo or just the large W design from the logo in white against a dark background, perhaps made up from the dark green in the logo.
The logos are attached so you can see the colours in them but the dark ones are..
Dark Blue = C:88, M:55, Y:44, K:28
Dark Green = C:87, M:53, Y:50, K:50
We sometimes also use a bright orange as an accent or highlight colour…
Orange: = C:0, M:39, Y:94, K:0

```html
<!DOCTYPE html>
<html lang="en">
<head>
<meta charset="utf-8">
<title>Korvantix Technologies – Business Card Concepts</title>
<link rel="stylesheet" href="https://fonts.googleapis.com/css2?family=Open+Sans:wght@400;600;700;800&display=swap">
<style>
  :root {
    --stage: #9c6b42;
    --card: #ffffff;
    --ink-dark: #1d4853;
    --ink-text: #2b3a40;
    --band-start: #3d6b76;
    --band-end: #a8c3c6;
    --band-block: #1e4651;
    --back-dark: #15414a;
    --back-accent: #2c5c66;
    --label: #2a1a0e;
  }
  * { box-sizing: border-box; margin: 0; padding: 0; }
  html, body { width: 1200px; height: 788px; overflow: hidden; }
  body {
    position: relative;
    background: var(--stage);
    font-family: "Open Sans", Arial, sans-serif;
    color: var(--ink-text);
  }
  .view-label {
    position: absolute;
    width: 502px;
    text-align: center;
    font-size: 20px;
    font-weight: 400;
    color: var(--label);
  }
  .card {
    position: absolute;
    width: 502px;
    height: 324px;
    border-radius: 18px;
    background: var(--card);
    overflow: hidden;
  }
  .card--front  { left: 66px;  top: 54px; }
  .card--back-1 { left: 626px; top: 54px; }
  .card--back-2 { left: 66px;  top: 444px; background: var(--back-dark); }
  .card--back-3 { left: 626px; top: 444px; }

  .brand {
    position: absolute;
    display: flex;
    align-items: center;
    color: var(--ink-dark);
    font-weight: 800;
    white-space: nowrap;
  }
  .brand__mark { background: var(--ink-dark); flex: none; }
  .brand__name { display: block; line-height: 1.08; }
  .brand__name span { display: block; }

  .card--front .brand { left: 26px; top: 118px; gap: 12px; font-size: 22px; }
  .card--front .brand__mark { width: 34px; height: 34px; }

  .name-band {
    position: absolute;
    left: 296px; top: 148px;
    width: 206px; height: 51px;
    background: linear-gradient(90deg, var(--band-start), var(--band-end));
    color: #fff;
    padding: 8px 0 0 13px;
  }
  .name-band::after {
    content: "";
    position: absolute;
    right: 0; top: 0;
    width: 30px; height: 100%;
    background: var(--band-block);
  }
  .name-band__name { font-size: 16px; font-weight: 700; line-height: 1.2; }
  .name-band__role { font-size: 12px; font-weight: 400; line-height: 1.3; }

  .contact-list {
    position: absolute;
    left: 302px; top: 222px;
    list-style: none;
    font-size: 12.5px;
  }
  .contact-list li {
    display: flex; align-items: center; gap: 6px;
    height: 21.5px;
  }
  .contact-list svg { width: 10px; height: 10px; fill: var(--ink-text); flex: none; }

  .address {
    position: absolute;
    left: 27px; top: 268px;
    font-size: 12.5px;
    line-height: 18px;
    font-style: normal;
  }

  .card--back-1 .brand {
    left: 50%; top: 130px; transform: translate(-50%, -50%);
    gap: 16px; font-size: 30px;
  }
  .card--back-1 .brand__mark { width: 60px; height: 60px; }

  .web-line {
    position: absolute;
    left: 0; width: 100%;
    text-align: center;
    font-size: 18px;
    letter-spacing: 2.2px;
    color: var(--ink-dark);
  }
  .card--back-1 .web-line { top: 284px; }
  .card--back-3 .web-line { top: 280px; }

  .card--back-2 .brand {
    left: 50%; top: 50%; transform: translate(-50%, -50%);
    font-size: 48px; color: var(--back-accent);
  }

  .card--back-3 .brand {
    left: 50%; top: 44px; transform: translateX(-50%);
    flex-direction: column; gap: 18px; font-size: 34px; text-align: center;
  }
  .card--back-3 .brand__mark { width: 80px; height: 80px; }
</style>
</head>
<body>
  <div class="view-label" style="left:66px; top:20px;">Front</div>
  <div class="view-label" style="left:626px; top:20px;">Back - 1</div>
  <div class="view-label" style="left:66px; top:403px;">Back - 2</div>
  <div class="view-label" style="left:626px; top:403px;">Back - 3</div>

  <section class="card card--front">
    <div class="brand"><span class="brand__mark"></span><span class="brand__name"><span>KORVANTIX</span><span>TECHNOLOGIES</span></span></div>
    <div class="name-band">
      <div class="name-band__name">Dennis Marlow</div>
      <div class="name-band__role">Operations Manager</div>
    </div>
    <ul class="contact-list">
      <li><svg viewBox="0 0 10 10"><path d="M2 0.5 L3.8 2.6 L2.8 3.8 Q4 6 6.2 7.2 L7.4 6.2 L9.5 8 L8.2 9.5 Q3 9 0.5 1.8 Z"/></svg>+44(0) 1632&nbsp; xxx xxx</li>
      <li><svg viewBox="0 0 10 10"><path d="M2.5 0 H7.5 V10 H2.5 Z M3.5 1.5 V7 H6.5 V1.5 Z"/></svg>+44(0) 7700 xxx xxx</li>
      <li><svg viewBox="0 0 10 10"><path d="M0 2 H10 V8.5 H0 Z M1 3 V7.5 H9 V3 L5 5.8 Z"/></svg>denmo@korvantix.example</li>
      <li><svg viewBox="0 0 10 10"><circle cx="5" cy="5" r="4.5"/></svg>www.korvantix.example</li>
    </ul>
    <address class="address">17 Pellick Row<br>Aberdeen AB12 9QZ</address>
  </section>

  <section class="card card--back-1">
    <div class="brand"><span class="brand__mark"></span><span class="brand__name"><span>KORVANTIX</span><span>TECHNOLOGIES</span></span></div>
    <div class="web-line">www.korvantix.example</div>
  </section>

  <section class="card card--back-2">
    <div class="brand"><span class="brand__name">KORVANTIX</span></div>
  </section>

  <section class="card card--back-3">
    <div class="brand"><span class="brand__mark"></span><span class="brand__name"><span>KORVANTIX</span><span>TECHNOLOGIES</span></span></div>
    <div class="web-line">www.korvantix.example</div>
  </section>
</body>
</html>
```